Managed IT services business card design

We haven't needed a business card since the founding of the business in 2005. All our clients have been coming through word of mouth. And lately more and more existing clients are requesting for our business cards to pass on to their contacts in recommending us.
So we needing a business card design. We use various innovative solutions and methodologies to provide IT services to small businesses in managing their IT systems. Our role is the same as an in-house, full-time IT Manager for our clients, but outsourced. So we take care of all our clients' IT needs, just as an IT Manager would be expected to perform.
We have a holding website, which we're happy to leave for now. If we can use the same logo would be great - www.lumadesk.com.au
Preferred colours are shades of are white, grey and black.
We pride our business with the following traits: proactive, good service, prompt response, trustworthy.
Target Market(s)
Small businesses of any industry
Industry/Entity Type
Business

```html
<!DOCTYPE html>
<html lang="en">
<head>
<meta charset="utf-8">
<title>Lumadesk business card</title>
<link rel="stylesheet" href="https://fonts.googleapis.com/css2?family=Montserrat:wght@400&family=Open+Sans:wght@400&display=swap">
<style>
  :root {
    --backdrop: #e4e5e6;
    --card-grey: #5b6064;
    --paper: #ffffff;
    --ink: #111111;
    --muted: #2e3235;
    --shadow: rgba(0, 0, 0, 0.28);
  }
  * { box-sizing: border-box; margin: 0; padding: 0; }
  html, body { width: 1200px; height: 680px; overflow: hidden; }
  body {
    background: var(--backdrop);
    font-family: "Open Sans", Arial, sans-serif;
    position: relative;
  }
  .card {
    position: absolute;
    top: 192px;
    width: 520px;
    height: 297px;
    border-radius: 24px;
    overflow: hidden;
    background: var(--card-grey);
    box-shadow: 0 8px 22px var(--shadow);
  }
  .card--front { left: 50px; }
  .card--back { left: 630px; }

  .front-art { position: absolute; inset: 0; width: 100%; height: 100%; }

  .brand {
    position: absolute;
    font-family: "Montserrat", Arial, sans-serif;
    font-weight: 400;
    letter-spacing: 0.32em;
    white-space: nowrap;
  }
  .brand--front {
    left: 36px; top: 112px;
    font-size: 30px;
    color: var(--ink);
  }
  .brand-mark {
    display: inline-block;
    width: 10px; height: 10px;
    margin-left: 4px;
    background: currentColor;
    vertical-align: middle;
  }

  .person {
    position: absolute;
    left: 352px; top: 58px;
    width: 150px;
    color: var(--paper);
  }
  .person__name { font-size: 15px; line-height: 1.2; }
  .person__role {
    font-size: 10px;
    color: var(--ink);
    text-align: right;
    padding-right: 20px;
  }

  .contact-list {
    position: absolute;
    left: 352px; top: 112px;
    list-style: none;
    color: var(--paper);
    font-size: 12px;
    line-height: 16px;
  }
  .contact-list li { display: flex; align-items: center; gap: 6px; white-space: nowrap; }
  .contact-icon { width: 10px; height: 10px; flex: none; }

  .address {
    position: absolute;
    left: 34px; bottom: 22px;
    color: var(--paper);
    font-size: 14px;
    line-height: 18px;
    font-style: normal;
  }

  .brand--back {
    left: 0; right: 0; top: 118px;
    text-align: center;
    font-size: 36px;
    color: var(--paper);
  }
  .web-line {
    position: absolute;
    right: 30px; bottom: 26px;
    color: var(--paper);
    font-size: 11px;
    letter-spacing: 0.3em;
  }
</style>
</head>
<body>

<section class="card card--front" aria-label="Business card front">
  <svg class="front-art" viewBox="0 0 520 297" aria-hidden="true">
    <path class="paper-panel" fill="var(--paper)" d="M0,0 H330 C322,130 220,232 0,232 Z"/>
    <path class="swoosh" fill="var(--ink)" d="M334,0 H348 C346,120 270,205 150,240 C262,196 326,120 334,0 Z"/>
  </svg>

  <div class="brand brand--front">lumadesk<span class="brand-mark"></span></div>

  <div class="person">
    <p class="person__name">Mark Tellan</p>
    <p class="person__role">director</p>
  </div>

  <ul class="contact-list">
    <li>555 014 2200
      <svg class="contact-icon" viewBox="0 0 10 10"><circle cx="5" cy="5" r="4.5" fill="var(--ink)"/><path d="M3,2.5 L4.3,2.5 L4.6,4 L3.9,4.5 Q4.6,5.8 5.6,6.2 L6.1,5.5 L7.5,5.8 L7.5,7 Q4,7.5 3,2.5 Z" fill="var(--paper)"/></svg>
    </li>
    <li>555 014 2201
      <svg class="contact-icon" viewBox="0 0 10 10"><rect x="1" y="4" width="8" height="5" fill="var(--ink)"/><rect x="2.5" y="1" width="5" height="3" fill="var(--ink)"/></svg>
    </li>
    <li>info@lumadesk.com.au
      <svg class="contact-icon" viewBox="0 0 10 10"><rect x="0.5" y="2" width="9" height="6.5" fill="var(--ink)"/><path d="M0.5,2 L5,5.5 L9.5,2" fill="none" stroke="var(--paper)" stroke-width="0.8"/></svg>
    </li>
    <li>www.lumadesk.com.au
      <svg class="contact-icon" viewBox="0 0 10 10"><circle cx="5" cy="5" r="4.5" fill="var(--ink)"/><path d="M0.5,5 H9.5 M5,0.5 V9.5 M1.5,2.8 H8.5 M1.5,7.2 H8.5" stroke="var(--card-grey)" stroke-width="0.6"/></svg>
    </li>
  </ul>

  <address class="address">1470 Calder Way Bd<br>Marlow NV 89120</address>
</section>

<section class="card card--back" aria-label="Business card back">
  <div class="brand brand--back">lumadesk<span class="brand-mark"></span></div>
  <p class="web-line">www.lumadesk.com.au</p>
</section>

</body>
</html>
```